Freelancer Information Security professional needs a business card

I need a simple, young, elegant business card. I'm a freelancer in the InfoSec area and want to be able to give my card to potential customers and new people I meet.

I'd like to have a clean, professional look but at same time not boring or corporate.

The only requirement is to have my "introduction" phrase which is:
"Half hacker, half mercenary."

I have added a card I have as a example, which I think it gives a good example of style I want.

Target Market(s)

Technology / Computers / Engineering

Industry/Entity Type

Information Technology

Contact Information for Business Card

Contact fields I want included:

(351) 93 618 20 54
tomas@vendoza.im
https://vendoza.im

Font styles to use
Sans Serif

Requirements
Nice to have
• Card doesn't need to have a doubled side, but it looks good / fits the design then please do include.
Should not have
• Outdated graphics or images; too much patterns/colors.

```html
<!DOCTYPE html>
<html lang="en">
<head>
<meta charset="utf-8">
<title>Tomas Vendoza — Business Card</title>
<link rel="stylesheet" href="https://fonts.googleapis.com/css2?family=Open+Sans:wght@700&family=Abel&display=swap">
<style>
  :root {
    --navy: #2c3588;
    --blue: #2a6fc2;
    --silver-edge: #c4c5c8;
    --silver-mid: #e6e7e9;
    --paper: #ffffff;
    --ink: #2b2b33;
    --line-blue: #4a5a9c;
    --mark-fill: #7a80b8;
    --shadow: rgba(0, 0, 0, 0.28);
  }
  html, body {
    margin: 0;
    padding: 0;
    width: 950px;
    height: 1200px;
    overflow: hidden;
    background: var(--paper);
  }
  .card {
    position: absolute;
    width: 771px;
    height: 450px;
    box-shadow: 8px 10px 14px var(--shadow);
    overflow: hidden;
  }
  .card-front { left: 96px; top: 61px; }
  .card-back {
    left: 93px; top: 651px;
    background: linear-gradient(90deg, var(--silver-edge) 0%, var(--silver-mid) 18%, var(--paper) 42%, var(--paper) 60%, var(--silver-mid) 82%, var(--silver-edge) 100%);
  }
  .card-art { position: absolute; inset: 0; }
  .holder-name, .tagline {
    position: absolute;
    left: 0; right: 0;
    margin: 0;
    text-align: center;
    color: var(--paper);
    font-family: "Open Sans", sans-serif;
    font-weight: 700;
    text-transform: uppercase;
  }
  .holder-name { top: 67px; font-size: 26px; letter-spacing: 0.5px; }
  .tagline { top: 134px; font-size: 19px; letter-spacing: 0.3px; }
  .contact-list {
    position: absolute;
    left: 267px;
    top: 268px;
    margin: 0;
    padding: 0;
    list-style: none;
    font-family: "Abel", sans-serif;
    font-size: 27px;
    color: var(--ink);
  }
  .contact-item {
    display: flex;
    align-items: center;
    height: 48px;
  }
  .contact-icon { width: 20px; height: 20px; margin-right: 13px; flex: none; }
  .mark-square {
    position: absolute;
    left: 568px; top: 248px;
    width: 196px; height: 196px;
    border: 2px solid var(--line-blue);
    background: rgba(122, 128, 184, 0.08);
  }
  .back-identity {
    position: absolute;
    inset: 0;
    display: flex;
    align-items: center;
    justify-content: center;
    gap: 16px;
  }
  .back-square { width: 26px; height: 26px; background: var(--navy); }
  .back-name {
    font-family: "Open Sans", sans-serif;
    font-weight: 700;
    font-size: 30px;
    text-transform: uppercase;
    color: var(--navy);
    letter-spacing: 0.5px;
  }
</style>
</head>
<body>

<section class="card card-front">
  <svg class="card-art" viewBox="0 0 771 450" preserveAspectRatio="none" aria-hidden="true">
    <defs>
      <linearGradient id="silver-body" x1="0" y1="0" x2="1" y2="0">
        <stop offset="0" stop-color="#c4c5c8"/>
        <stop offset="0.2" stop-color="#e6e7e9"/>
        <stop offset="0.45" stop-color="#ffffff"/>
        <stop offset="0.65" stop-color="#ffffff"/>
        <stop offset="0.85" stop-color="#e6e7e9"/>
        <stop offset="1" stop-color="#c4c5c8"/>
      </linearGradient>
      <linearGradient id="header-blue" x1="0" y1="0" x2="0" y2="1">
        <stop offset="0" stop-color="#2c3588"/>
        <stop offset="1" stop-color="#2a70c4"/>
      </linearGradient>
      <linearGradient id="swoosh" x1="0" y1="0" x2="1" y2="0">
        <stop offset="0" stop-color="#d8d9dc"/>
        <stop offset="0.35" stop-color="#9a9ca3"/>
        <stop offset="0.55" stop-color="#ffffff"/>
        <stop offset="0.8" stop-color="#8e9097"/>
        <stop offset="1" stop-color="#d0d1d4"/>
      </linearGradient>
    </defs>
    <rect width="771" height="450" fill="url(#silver-body)"/>
    <path d="M0 190 Q 380 242 771 198 L 771 212 Q 380 262 0 204 Z" fill="url(#swoosh)"/>
    <path d="M0 0 H771 V186 Q 380 234 0 178 Z" fill="url(#header-blue)"/>
    <path d="M0 178 Q 380 234 771 186" fill="none" stroke="#2c2f80" stroke-width="3"/>
  </svg>

  <h1 class="holder-name">Tomas Vendoza</h1>
  <p class="tagline">Half hacker, half mercenary.</p>

  <ul class="contact-list">
    <li class="contact-item">
      <svg class="contact-icon" viewBox="0 0 20 20" aria-hidden="true">
        <rect x="5" y="2" width="10" height="16" rx="1.5" fill="none" stroke="#2c3588" stroke-width="1.6"/>
        <line x1="8.5" y1="15" x2="11.5" y2="15" stroke="#2c3588" stroke-width="1.4"/>
      </svg>
      <span>(351) 93 618 20 54</span>
    </li>
    <li class="contact-item">
      <svg class="contact-icon" viewBox="0 0 20 20" aria-hidden="true">
        <rect x="2" y="5" width="16" height="11" fill="none" stroke="#2c3588" stroke-width="1.5"/>
        <path d="M2 5 L10 11.5 L18 5" fill="none" stroke="#2c3588" stroke-width="1.5"/>
      </svg>
      <span>tomas@vendoza.im</span>
    </li>
    <li class="contact-item">
      <svg class="contact-icon" viewBox="0 0 20 20" aria-hidden="true">
        <circle cx="10" cy="10" r="7.5" fill="none" stroke="#2c3588" stroke-width="1.4"/>
        <ellipse cx="10" cy="10" rx="3.3" ry="7.5" fill="none" stroke="#2c3588" stroke-width="1.2"/>
        <line x1="2.5" y1="10" x2="17.5" y2="10" stroke="#2c3588" stroke-width="1.2"/>
      </svg>
      <span>https://vendoza.im</span>
    </li>
  </ul>

  <div class="mark-square" aria-hidden="true"></div>
</section>

<section class="card card-back">
  <div class="back-identity">
    <span class="back-square" aria-hidden="true"></span>
    <span class="back-name">Tomas Vendoza</span>
  </div>
</section>

</body>
</html>
```